Business Card Design

New business card design

Target Market(s)

Residential & Commercial Property Managers

Industry/Entity Type

Plumbing Services

Contact Information for Business Card

Name - Rowan Keddle, title - Director, Phone Number - 0431 286 517, email - rowan@tbk-plumbing.com.au, Company ABN - 73 215 904 386,

Font styles to use
Sans Serif

Colors
0054AA
0677BA
7BADD7
CADEEF
E8F1F8

```html
<!DOCTYPE html>
<html lang="en">
<head>
<meta charset="utf-8">
<title>TBK Plumbing Services – Business Card</title>
<link rel="stylesheet" href="https://fonts.googleapis.com/css2?family=Arimo:wght@400;700&display=swap">
<style>
  :root {
    --bg: #e4e5e7;
    --card: #ffffff;
    --ink: #1b2129;
    --blue: #29a8e0;
    --grey: #555b63;
  }
  * { box-sizing: border-box; margin: 0; padding: 0; }
  html, body { width: 1200px; height: 800px; overflow: hidden; }
  body {
    background: var(--bg);
    font-family: "Arimo", Arial, sans-serif;
    position: relative;
  }
  .card {
    position: absolute;
    top: 248px;
    width: 500px;
    height: 305px;
    background: var(--card);
    overflow: hidden;
    box-shadow: 0 6px 18px rgba(0,0,0,.12);
  }
  .card--front { left: 70px; }
  .card--back { left: 630px; }

  .company-name {
    position: absolute;
    font-size: 30px;
    font-weight: 700;
    color: var(--ink);
    line-height: 1.1;
    white-space: nowrap;
  }
  .card--front .company-name { left: 70px; top: 112px; }
  .card--back .company-name { left: 40px; top: 42px; }

  .website {
    position: absolute;
    right: 30px;
    top: 30px;
    font-size: 15px;
    letter-spacing: 2.5px;
    color: var(--ink);
    white-space: nowrap;
  }
  .website__domain { color: var(--blue); }

  .band { position: absolute; background: var(--ink); }
  .tab { position: absolute; background: var(--blue); }

  .card--front .band { left: 0; bottom: 48px; width: 340px; height: 22px; }
  .card--front .tab {
    right: 0; bottom: 0; width: 190px; height: 80px;
    border-top-left-radius: 34px;
  }

  .card--back .band { left: 190px; right: 0; bottom: 40px; height: 24px; }
  .card--back .tab {
    left: 0; bottom: 40px; width: 205px; height: 72px;
    border-top-right-radius: 26px;
    display: flex; align-items: center; padding-left: 22px;
  }
  .abn {
    font-size: 14px;
    font-weight: 700;
    color: var(--ink);
    white-space: nowrap;
  }

  .contact {
    position: absolute;
    right: 28px;
    bottom: 82px;
    text-align: right;
    color: var(--grey);
  }
  .contact__name { font-size: 17px; font-weight: 700; color: var(--ink); }
  .contact__title { font-size: 13px; margin-bottom: 10px; }
  .contact__line {
    font-size: 13px;
    display: flex; align-items: center; justify-content: flex-end; gap: 6px;
    margin-top: 4px;
    white-space: nowrap;
  }
  .contact__icon { width: 12px; height: 12px; fill: var(--blue); }
</style>
</head>
<body>

  <section class="card card--front" aria-label="Business card front">
    <div class="website">www.<span class="website__domain">tbkplumbingservices</span>.com.au</div>
    <div class="company-name">TBK Plumbing Services</div>
    <div class="band"></div>
    <div class="tab"></div>
  </section>

  <section class="card card--back" aria-label="Business card back">
    <div class="company-name">TBK Plumbing Services</div>

    <div class="contact">
      <div class="contact__name">Rowan Keddle</div>
      <div class="contact__title">Director</div>
      <div class="contact__line">0431 286 517
        <svg class="contact__icon" viewBox="0 0 24 24" aria-hidden="true"><path d="M6.6 10.8a15.1 15.1 0 0 0 6.6 6.6l2.2-2.2a1 1 0 0 1 1-.25 11.4 11.4 0 0 0 3.6.57 1 1 0 0 1 1 1V20a1 1 0 0 1-1 1A17 17 0 0 1 3 4a1 1 0 0 1 1-1h3.5a1 1 0 0 1 1 1c0 1.25.2 2.45.57 3.6a1 1 0 0 1-.25 1z"/></svg>
      </div>
      <div class="contact__line">rowan@tbk-plumbing.com.au
        <svg class="contact__icon" viewBox="0 0 24 24" aria-hidden="true"><path d="M2 5h20v14H2z M3.5 6.5 12 13l8.5-6.5" fill="var(--blue)" stroke="#fff" stroke-width="1.5"/></svg>
      </div>
    </div>

    <div class="band"></div>
    <div class="tab"><span class="abn">ABN - 73 215 904 386</span></div>
  </section>

</body>
</html>
```